The Linen Loft Co

We need a business card design for our wardrobe company.
Please visit our website www.gentlelinenlofts.com to get an idea of who we are.

```html
<!DOCTYPE html>
<html lang="en">
<head>
<meta charset="utf-8">
<title>The Linen Loft Co – Business Card</title>
<link rel="stylesheet" href="https://fonts.googleapis.com/css2?family=Roboto:wght@400;500;700&display=swap">
<style>
  :root {
    --backdrop: #2a2724;
    --card-dark: #0d0d0d;
    --card-light: #ffffff;
    --ink: #111111;
    --ink-soft: #555555;
    --ink-muted: #b5b5b5;
  }
  * { margin: 0; padding: 0; box-sizing: border-box; }
  html, body {
    width: 1200px;
    height: 801px;
    overflow: hidden;
    background: var(--backdrop);
    font-family: "Roboto", sans-serif;
  }
  .stage {
    position: relative;
    width: 1200px;
    height: 801px;
  }
  .business-card {
    position: absolute;
    left: 150px;
    top: 143px;
    width: 900px;
    height: 514px;
    background: var(--card-dark);
    overflow: hidden;
  }
  .card-face {
    position: absolute;
    inset: 0;
    width: 900px;
    height: 514px;
  }
  .card-face path { fill: var(--card-light); }

  .brand {
    position: absolute;
    left: 580px;
    top: 190px;
    display: flex;
    align-items: center;
    gap: 14px;
  }
  .brand-mark {
    width: 22px;
    height: 22px;
    background: var(--ink);
  }
  .brand-name {
    font-size: 21px;
    font-weight: 500;
    letter-spacing: 0.5px;
    text-transform: uppercase;
    color: var(--ink);
  }

  .holder {
    position: absolute;
    left: 38px;
    top: 222px;
  }
  .holder-name {
    font-size: 36px;
    font-weight: 700;
    color: var(--ink);
    line-height: 1;
  }
  .holder-role {
    margin-top: 2px;
    font-size: 21px;
    font-weight: 400;
    color: var(--ink-muted);
  }

  .contacts {
    position: absolute;
    left: 38px;
    top: 302px;
    list-style: none;
  }
  .contacts li {
    display: flex;
    align-items: center;
    gap: 12px;
    font-size: 21px;
    color: var(--ink-soft);
    line-height: 30px;
  }
  .contacts svg {
    width: 18px;
    height: 18px;
    flex: none;
    fill: var(--ink);
  }

  .divider {
    position: absolute;
    left: 458px;
    top: 378px;
    width: 2px;
    height: 56px;
    background: var(--ink);
  }
  .address {
    position: absolute;
    left: 480px;
    top: 380px;
    font-size: 21px;
    color: var(--ink-soft);
    line-height: 27px;
    font-style: normal;
  }
</style>
</head>
<body>
<main class="stage">
  <article class="business-card">
    <svg class="card-face" viewBox="0 0 900 514" aria-hidden="true">
      <path d="M0,514 L0,310 C0,130 120,22 310,0 L900,0 L900,290 C900,440 800,506 640,514 Z"/>
    </svg>

    <div class="brand">
      <span class="brand-mark"></span>
      <span class="brand-name">The Linen Loft Co</span>
    </div>

    <header class="holder">
      <h1 class="holder-name">Daniel Hart</h1>
      <p class="holder-role">President</p>
    </header>

    <ul class="contacts">
      <li>
        <svg viewBox="0 0 24 24"><path d="M6.6 10.8a15.1 15.1 0 0 0 6.6 6.6l2.2-2.2a1 1 0 0 1 1-.25 11.4 11.4 0 0 0 3.6.57 1 1 0 0 1 1 1V20a1 1 0 0 1-1 1A17 17 0 0 1 3 4a1 1 0 0 1 1-1h3.5a1 1 0 0 1 1 1c0 1.25.2 2.45.57 3.57a1 1 0 0 1-.25 1z"/></svg>
        020 7946 0183
      </li>
      <li>
        <svg viewBox="0 0 24 24"><path d="M2 5h20v14H2z M4 7v.4l8 5 8-5V7z" fill-rule="evenodd"/></svg>
        info@gentlelinenlofts.com
      </li>
      <li>
        <svg viewBox="0 0 24 24"><path d="M12 2a10 10 0 1 0 0 20 10 10 0 0 0 0-20zm-1 17.9A8 8 0 0 1 4.1 11H7c.1 3.2 1.5 6.3 4 8.9zM4.1 9A8 8 0 0 1 11 4.1C8.5 6.7 7.1 6 7 9zm8.9 10.9c2.5-2.6 3.9-5.7 4-8.9h2.9a8 8 0 0 1-6.9 8.9zM17 9c-.1-3-1.5-2.3-4-4.9A8 8 0 0 1 19.9 9z"/></svg>
        www.gentlelinenlofts.com
      </li>
    </ul>

    <span class="divider"></span>
    <address class="address">Harbour House, 42 Mill Lane,<br>London N1 7QT</address>
  </article>
</main>
</body>
</html>
```